Wireless Internet Service Provider website design

We need a Internet Service Provider website that show the packages that we offer as well as the functionality where customers have the option of clicking on the various packages and be linked to a page where they can sign up for our services.
We need about 10-15 pages.
A. Integrated online store.
B. Live chat.
C. Social media page
My old website. Brightlinkradio.nyc

Example: http://plumcrestnet.com/services/residential/ Added Tuesday, June 7, 2016

Target Market(s)

Residential and small businesses

Industry/Entity Type

Internet

Coding

Coded - Design and coding required

Number of Pages Required

5+ page

Font styles to use
Serif
Sans Serif
Script

Colors
3176b5
85cae6
ffffff

Requirements
Must have
• Online store and live chat, drop down details on pricing from current website
Nice to have
• great design, functional website,

```html
<!DOCTYPE html>
<html lang="en">
<head>
<meta charset="utf-8">
<title>BrightlinkRadio – Wireless Internet</title>
<link href="https://fonts.googleapis.com/css2?family=Montserrat:wght@400;600;700&family=Open+Sans:ital,wght@0,400;0,600;0,700;1,400&display=swap" rel="stylesheet">
<style>
:root{
  --blue:#2f6fb3;
  --blue-dark:#2a5f9e;
  --sky:#2bb7cf;
  --ink:#333;
  --muted:#666;
  --light:#f3f3f3;
  --card:#ececec;
  --charcoal:#3b3d42;
  --footer:#222;
  --white:#fff;
}
*{box-sizing:border-box;margin:0;padding:0}
html,body{width:1200px;height:2359px;overflow:hidden}
body{position:relative;font-family:"Open Sans",Arial,sans-serif;color:var(--ink);background:var(--white)}
.abs{position:absolute}
.heading{font-family:"Montserrat",Arial,sans-serif;font-weight:700;color:var(--blue)}

/* header */
.header{left:0;top:0;width:1200px;height:88px;background:var(--white);border-top:4px solid var(--blue);box-shadow:0 1px 3px rgba(0,0,0,.1);z-index:3}
.topbar{right:100px;top:16px;font-size:12px;color:var(--muted);display:flex;gap:22px;align-items:center}
.topbar .phone{color:var(--ink);display:flex;gap:7px;align-items:center}
.nav{right:100px;top:52px;display:flex;gap:0;font-family:"Montserrat",sans-serif;font-size:12.5px;font-weight:600;color:#222}
.nav span{margin-left:58px}
.nav .active{color:var(--blue)}
.logo-box{left:99px;top:0;width:205px;height:142px;background:var(--white);border-radius:0 0 8px 8px;box-shadow:0 2px 6px rgba(0,0,0,.25);z-index:4;display:flex;align-items:flex-end;justify-content:center;padding-bottom:34px;gap:8px}
.logo-box .mark{width:22px;height:22px;border-radius:50%;background:var(--blue)}
.logo-box .name{font-family:"Montserrat",sans-serif;font-weight:600;font-size:19px;color:#555}

/* hero */
.hero{left:0;top:88px;width:1200px;height:514px;background:radial-gradient(circle at 420px 230px,#f7c35a 0,#d98418 14%,#6b3a0c 36%,#1b1209 62%,#0a0806 100%)}
.hero-title{right:100px;top:288px;font-family:"Montserrat",sans-serif;font-weight:700;font-size:45px;color:var(--white);text-align:right}
.hero-text{right:100px;top:346px;width:460px;font-size:13px;line-height:26px;color:var(--white);text-align:right}
.hero-link{right:100px;top:404px;font-size:12px;font-weight:600;color:var(--white);text-decoration:underline}
.arrow{top:325px;width:16px;height:46px}

/* welcome */
.welcome-title{left:0;top:646px;width:1200px;text-align:center;font-size:30px}
.welcome-title .grey{color:#6d6d6d}
.intro{left:0;width:1200px;text-align:center;font-size:13px;line-height:26px;color:var(--muted)}
.service{width:300px;text-align:center}
.service .ring{margin:0 auto;width:88px;height:88px;border:3px solid var(--blue);border-radius:50%;display:flex;align-items:center;justify-content:center}
.service h3{margin-top:22px;font-size:14px;font-weight:700;color:var(--blue)}
.service p{margin-top:6px;font-size:12.5px;line-height:24px;color:var(--muted)}
.service a{display:block;margin-top:6px;font-size:11.5px;font-weight:600;color:var(--sky);text-decoration:underline}

/* plans */
.plans{left:0;top:1019px;width:1200px;height:612px;background:var(--light)}
.plans-title{left:0;top:1064px;width:1200px;text-align:center;font-size:26px}
.plan{top:1225px;width:223px;height:343px;background:var(--card);text-align:center}
.plan .price{position:absolute;left:68px;top:-49px;width:86px;height:86px;border-radius:50%;background:var(--charcoal);color:var(--white);display:flex;flex-direction:column;align-items:center;justify-content:center;font-size:19px;font-weight:600}
.plan .price small{font-size:10px;font-weight:400;margin-top:-2px}
.plan h4{margin-top:59px;font-family:"Montserrat",sans-serif;font-size:14.5px;font-weight:600;color:#333}
.plan ul{list-style:none;margin:12px auto 0;width:180px}
.plan li{height:44px;line-height:44px;font-size:13px;color:var(--muted);border-bottom:1px solid #dcdcdc}
.plan li:last-child{border-bottom:none}
.plan .btn{position:absolute;left:44px;top:282px;width:135px;height:35px;background:var(--charcoal);color:var(--white);font-family:"Montserrat",sans-serif;font-size:12.5px;font-weight:700;line-height:35px}
.plan.featured{background:var(--blue)}
.plan.featured .price{background:var(--sky)}
.plan.featured h4,.plan.featured li{color:var(--white)}
.plan.featured li{border-bottom-color:rgba(255,255,255,.3)}
.plan.featured .btn{background:var(--sky);top:276px}

/* news & testimonials */
.col-title{font-size:21px;width:470px;border-bottom:2px solid #d5d5d5;padding-bottom:10px}
.pager{top:1694px;display:flex;gap:2px}
.pager span{width:17px;height:17px;background:#bbb}
.pager span+span{background:#777}
.news-item{left:99px;width:470px}
.date{width:63px;height:67px;text-align:center;color:var(--white)}
.date .day{height:44px;background:#333;font-size:24px;line-height:44px}
.date .mon{height:23px;background:var(--blue);font-size:10px;line-height:23px}
.news-body{position:absolute;left:75px;top:-4px}
.news-body h5{font-size:14.5px;font-weight:600;color:var(--blue)}
.news-body p{margin-top:4px;font-size:12.5px;line-height:22px;color:var(--muted)}
.avatar{left:632px;top:1758px;width:110px;height:110px;border-radius:50%;border:4px solid #ddd;background:radial-gradient(circle at 50% 40%,#6c8ea8,#2e4e68)}
.quote{left:762px;top:1758px;width:338px;font-size:12.5px;font-style:italic;line-height:26px;color:var(--muted);text-align:justify}
.quote .q{font-size:30px;color:#bbb;font-style:normal;line-height:0}
.author{left:768px;top:1874px;font-size:14px;font-weight:700;color:var(--blue)}

/* footer */
.footer{left:0;top:2065px;width:1200px;height:294px;background:var(--footer)}
.strip{left:99px;top:1999px;width:1000px;height:105px;background:var(--light);border:1px solid #ddd;z-index:2}
.feature{top:28px;display:flex;gap:14px;align-items:center}
.feature .dot{width:58px;height:58px;border-radius:50%;background:var(--blue);display:flex;align-items:center;justify-content:center}
.feature h6{font-size:14px;font-weight:700;color:var(--blue)}
.feature i{font-size:11.5px;color:#888}
.foot-h{top:2140px;font-size:14.5px;font-weight:700;color:var(--white)}
.contact{left:99px;top:2176px;font-size:12.5px;line-height:22px;color:#ddd}
.contact .row{display:flex;gap:16px;margin-bottom:8px}
.contact svg{flex:none;margin-top:4px}
.email-input{left:464px;top:2177px;width:245px;height:38px;background:var(--white);font-size:12px;font-style:italic;color:#999;line-height:38px;padding-left:12px}
.subscribe{left:719px;top:2177px;width:89px;height:38px;background:var(--blue);color:var(--white);font-size:12px;font-weight:700;text-align:center;line-height:38px}
.hint{left:464px;top:2226px;font-size:11px;font-style:italic;color:#aaa}
.social{left:951px;top:2175px;display:flex;gap:7px}
.social span{width:25px;height:25px;border-radius:50%;border:1.5px solid #ddd}
.social span:first-child{background:var(--blue);border-color:var(--blue)}
.bottom{left:0;top:2297px;width:1200px;height:62px;border-top:1px solid #3a3a3a;text-align:center;font-size:12px;color:#ddd;line-height:58px}
.chat{left:1164px;top:2079px;width:36px;height:150px;background:var(--sky);border-radius:6px 0 0 6px;color:var(--white);font-size:12px;font-weight:700;writing-mode:vertical-rl;transform:rotate(180deg);text-align:center;line-height:36px;border-radius:0 6px 6px 0}
</style>
</head>
<body>

<header class="abs header">
  <div class="abs topbar">
    <span class="phone"><svg width="11" height="11" viewBox="0 0 24 24"><path fill="#2f6fb3" d="M6.6 10.8a15 15 0 006.6 6.6l2.2-2.2c.3-.3.7-.4 1-.2 1.1.4 2.3.6 3.6.6.6 0 1 .4 1 1V20c0 .6-.4 1-1 1A17 17 0 013 4c0-.6.4-1 1-1h3.5c.6 0 1 .4 1 1 0 1.3.2 2.5.6 3.6.1.3 0 .7-.2 1z"/></svg>(866) 555-0142</span>
    <span>MY ACCOUNT &nbsp;|&nbsp; SHOPPING CART</span>
  </div>
  <nav class="abs nav">
    <span class="active">HOME</span><span>WHY BRIGHTLINK</span><span>PLANS &amp; PACKAGES</span><span>MY ACCOUNT</span><span>GALLERY</span>
    <span style="margin-left:40px"><svg width="12" height="12" viewBox="0 0 24 24"><circle cx="10" cy="10" r="7" fill="none" stroke="#222" stroke-width="3"/><path d="M15 15l7 7" stroke="#222" stroke-width="3"/></svg></span>
  </nav>
</header>
<div class="abs logo-box"><span class="mark"></span><span class="name">BrightlinkRadio</span></div>

<section class="abs hero" role="img" aria-label="Hand holding a glowing globe surrounded by a network of connected devices"></section>
<svg class="abs arrow" style="left:34px" viewBox="0 0 16 46"><path d="M14 2L3 23l11 21" fill="none" stroke="rgba(255,255,255,.6)" stroke-width="1.5"/></svg>
<svg class="abs arrow" style="right:34px" viewBox="0 0 16 46"><path d="M2 2l11 21L2 44" fill="none" stroke="rgba(255,255,255,.6)" stroke-width="1.5"/></svg>
<h1 class="abs hero-title">BRIGHTLINKRADIO</h1>
<p class="abs hero-text">When choosing among the best high speed internet providers, there are several other factors that should be taken into consideration besides</p>
<span class="abs hero-link">READ MORE</span>

<h2 class="abs heading welcome-title">WELCOME TO <span class="grey">BrightlinkRadio</span></h2>
<p class="abs intro" style="top:692px">When choosing among the best high speed internet providers, there are several other factors that should be taken into consideration besides just the<br>available download speeds. Upload speeds are important as well, though they probably are not as crucial</p>

<div class="abs service" style="left:120px;top:777px">
  <div class="ring"><svg width="30" height="32" viewBox="0 0 30 32"><circle cx="15" cy="9" r="7" fill="#2f6fb3"/><path d="M2 31c0-8 6-13 13-13s13 5 13 13z" fill="#2f6fb3"/></svg></div>
  <h3>RESIDENTIAL INTERNET</h3>
  <p>When choosing among the best high speed<br>internet providers, there are</p>
  <a>READ MORE</a>
</div>
<div class="abs service" style="left:446px;top:777px">
  <div class="ring"><svg width="36" height="30" viewBox="0 0 36 30"><rect x="13" y="1" width="10" height="8" fill="#2f6fb3"/><path d="M18 9v6M5 15h26M5 15v5M18 15v5M31 15v5" stroke="#2f6fb3" stroke-width="2" fill="none"/><rect x="0" y="20" width="10" height="8" fill="#2f6fb3"/><rect x="13" y="20" width="10" height="8" fill="#2f6fb3"/><rect x="26" y="20" width="10" height="8" fill="#2f6fb3"/></svg></div>
  <h3>BUSINESS INTERNET ACCESS</h3>
  <p>When choosing among the best high speed<br>internet providers, there are</p>
  <a>READ MORE</a>
</div>
<div class="abs service" style="left:761px;top:777px">
  <div class="ring"><svg width="36" height="36" viewBox="0 0 36 36" fill="none" stroke="#2f6fb3" stroke-width="2"><circle cx="18" cy="18" r="16"/><ellipse cx="18" cy="18" rx="7" ry="16"/><path d="M2 18h32M5 9h26M5 27h26M18 2v32"/></svg></div>
  <h3>UNLIMITED INTERNET USAGE</h3>
  <p>When choosing among the best high speed<br>internet providers, there are</p>
  <a>READ MORE</a>
</div>

<section class="abs plans"></section>
<h2 class="abs heading plans-title">PLAN &amp; PACKAGES</h2>
<p class="abs intro" style="top:1108px">When choosing among the best high speed internet providers, there are several other factors that should be taken into consideration besides just<br>the available download speeds. Upload speeds are important as well, though they probably are not as crucial</p>

<div class="abs plan" style="left:99px">
  <div class="price">$39.99<small>mo./1yr</small></div>
  <h4>BRIGHTLINK SIMPLICITY</h4>
  <ul><li>Free smart router</li><li>Free internet protection</li><li>Unlimited Brightlink</li><li>Wi-Fi access</li></ul>
  <div class="btn">SIGN UP</div>
</div>
<div class="abs plan" style="left:359px">
  <div class="price">$49.95<small>mo/1yr</small></div>
  <h4>BRIGHTLINK VALUE PAK</h4>
  <ul><li>Free smart router</li><li>Free internet protection</li><li>Unlimited Brightlink</li><li>Wi-Fi access</li></ul>
  <div class="btn">SIGN UP</div>
</div>
<div class="abs plan featured" style="left:620px">
  <div class="price">$ 69.99<small>mo./1yr</small></div>
  <h4>BRIGHTLINK SUPER-PAK</h4>
  <ul><li>Free smart router</li><li>Free internet protection</li><li>Unlimited Brightlink</li><li>Wi-Fi access</li></ul>
  <div class="btn">SIGN UP</div>
</div>
<div class="abs plan" style="left:878px">
  <div class="price">$89.99<small>mo./1yr</small></div>
  <h4>BRIGHTLINK ACTION PAK</h4>
  <ul><li>Free smart router</li><li>Free internet protection</li><li>Unlimited Brightlink</li><li>Wi-Fi access</li></ul>
  <div class="btn">SIGN UP</div>
</div>

<h2 class="abs heading col-title" style="left:99px;top:1688px">LATEST NEWS</h2>
<div class="abs pager" style="left:531px"><span></span><span></span></div>
<div class="abs news-item" style="top:1758px">
  <div class="date"><div class="day">02</div><div class="mon">JUNE</div></div>
  <div class="news-body"><h5>FAST DOWNLOAD &amp; UPLOAD</h5><p>When choosing among the best high speed internet providers,<br>there are several other factors</p></div>
</div>
<div class="abs" style="left:99px;top:1852px;width:470px;height:1px;background:#e2e2e2"></div>
<div class="abs news-item" style="top:1877px">
  <div class="date"><div class="day">02</div><div class="mon">JUNE</div></div>
  <div class="news-body"><h5>SPEEDS AT AN AFFORDABLE PRICE</h5><p>When choosing among the best high speed internet providers,<br>there are several other factors</p></div>
</div>

<h2 class="abs heading col-title" style="left:632px;top:1688px">TESTIMONIALS</h2>
<div class="abs pager" style="left:1064px"><span></span><span></span></div>
<div class="abs avatar" role="img" aria-label="Portrait photo of a smiling customer"></div>
<p class="abs quote"><span class="q">&ldquo;</span> When choosing among the best high speed internet providers, there are several other factors that should be taken into consideration besides just the available download speeds. Upload speeds are important as well <span class="q">&rdquo;</span></p>
<p class="abs author">- MARCUS DELANEY</p>

<footer class="abs footer"></footer>
<div class="abs strip">
  <div class="abs feature" style="left:28px"><span class="dot"><svg width="28" height="24" viewBox="0 0 28 24"><path d="M14 2C7 2 2 6 2 11c0 3 2 5 4 6l-2 5 6-3c1 .3 2 .4 4 .4 7 0 12-4 12-9S21 2 14 2z" fill="none" stroke="#fff" stroke-width="2"/></svg></span><div><h6>CUSTOMER SUPPORT</h6><i>Click here for more Info</i></div></div>
  <div class="abs feature" style="left:354px"><span class="dot"><svg width="26" height="26" viewBox="0 0 24 24"><path fill="#fff" d="M19.4 13a7.5 7.5 0 000-2l2.1-1.6-2-3.5-2.5 1a7 7 0 00-1.7-1L15 3h-4l-.4 2.7a7 7 0 00-1.7 1l-2.5-1-2 3.5L6.5 11a7.5 7.5 0 000 2l-2.1 1.6 2 3.5 2.5-1a7 7 0 001.7 1L11 21h4l.4-2.7a7 7 0 001.7-1l2.5 1 2-3.5zM13 15.5a3.5 3.5 0 110-7 3.5 3.5 0 010 7z"/></svg></span><div><h6>EQUIPMENT OPTIONS</h6><i>Click here for more Info</i></div></div>
  <div class="abs feature" style="left:714px"><span class="dot"><svg width="26" height="26" viewBox="0 0 24 24"><path fill="#fff" d="M2 10h4v11H2zM8 21V10l5-8c1.5 0 2.5 1 2.2 2.5L14.5 9H21c1 0 2 1 1.7 2.2l-2 8.3c-.3.9-1 1.5-2 1.5z"/></svg></span><div><h6>CUSTOMER GUARANTEE</h6><i>Click here for more Info</i></div></div>
</div>

<h3 class="abs foot-h" style="left:99px">CONTACT US</h3>
<div class="abs contact">
  <div class="row"><svg width="10" height="14" viewBox="0 0 10 14"><path d="M5 0a5 5 0 00-5 5c0 4 5 9 5 9s5-5 5-9a5 5 0 00-5-5zm0 7a2 2 0 110-4 2 2 0 010 4z" fill="#fff"/></svg><span>2480 Harbor Avenue 3rd Fl<br>Brooklyn, NY 11201</span></div>
  <div class="row"><svg width="12" height="12" viewBox="0 0 24 24"><path fill="#fff" d="M6.6 10.8a15 15 0 006.6 6.6l2.2-2.2c.3-.3.7-.4 1-.2 1.1.4 2.3.6 3.6.6.6 0 1 .4 1 1V20c0 .6-.4 1-1 1A17 17 0 013 4c0-.6.4-1 1-1h3.5c.6 0 1 .4 1 1 0 1.3.2 2.5.6 3.6.1.3 0 .7-.2 1z"/></svg><span>(866) 555 - 0187</span></div>
  <div class="row"><svg width="13" height="10" viewBox="0 0 13 10"><rect width="13" height="10" rx="1" fill="#fff"/><path d="M0 1l6.5 5L13 1" stroke="#222" fill="none"/></svg><span>Contact@brightlinkradio.nyc</span></div>
</div>

<h3 class="abs foot-h" style="left:464px">NEWS LETTER</h3>
<div class="abs email-input">Enter Email</div>
<div class="abs subscribe">SUBSCRIBE</div>
<p class="abs hint">* best time to contact you back!</p>

<h3 class="abs foot-h" style="left:951px">FOLLOW US</h3>
<div class="abs social"><span></span><span></span><span></span><span></span><span></span></div>

<div class="abs bottom">Copyright © 2016brightlinkradio.nyc. All Rights are Reserved</div>
<div class="abs chat">CHAT NOW !</div>

</body>
</html>
```